Brookvane Consulting Business Card Design

Business Card Design for Brookvane Consulting. Brookvane Consulting is a boutique consultancy based in Atlanta, GA., that specializes in marketing strategy, organization planning, and leadership development. We provide solutions for small businesses and startups as well as Vantage 300 companies.

http://brookvaneconsulting.com/

Target Market(s)

We provide solutions for small businesses and startups as well as Vantage 300 companies.

Industry/Entity Type

Consulting

Contact Information for Business Card

Two sided business card with priority on contact information, logo, tag line (Inspiration to Dream More, Do More, Become More)

Colors

Designer to choose colors to be used in the design.

Requirements
Must have
• contact information, logo, tag line (Inspiration to Dream More, Do More, Become More)
• Simple no over communication.
Nice to have
• I would like to see different placements of logo and creative use of both sides of the card
Should not have
• Do not put too much information on the card.

```html
<!DOCTYPE html>
<html lang="en">
<head>
<meta charset="utf-8">
<title>Brookvane Consulting Business Card</title>
<link rel="stylesheet" href="https://fonts.googleapis.com/css2?family=Courgette&family=Lato:wght@300;400;700&display=swap">
<style>
  :root {
    --stage: #ecebe8;
    --card-dark: #111111;
    --card-dark-top: #262626;
    --card-light: #ffffff;
    --ink: #2b2b2b;
    --ink-soft: #555555;
    --rule: #8a8a8a;
    --on-dark: #f2f2f2;
  }
  * { box-sizing: border-box; margin: 0; padding: 0; }
  html, body { width: 1200px; height: 900px; overflow: hidden; }
  body {
    background: var(--stage);
    font-family: "Lato", Arial, sans-serif;
    display: flex;
    align-items: center;
    justify-content: center;
    gap: 50px;
  }
  .card {
    position: relative;
    width: 540px;
    height: 309px;
    box-shadow: 0 10px 28px rgba(0,0,0,0.18);
  }
  .card--back {
    background: linear-gradient(180deg, var(--card-dark-top), var(--card-dark) 55%);
    color: var(--on-dark);
    display: flex;
    flex-direction: column;
    align-items: center;
    justify-content: center;
    text-align: center;
  }
  .tagline {
    font-family: "Courgette", cursive;
    font-size: 33px;
    line-height: 1.25;
    font-weight: 400;
    letter-spacing: 1px;
  }
  .back-url {
    margin-top: 36px;
    font-size: 13px;
    letter-spacing: 4px;
    font-weight: 400;
  }
  .card--front { background: var(--card-light); color: var(--ink); }
  .brand {
    position: absolute;
    top: 40px;
    right: 34px;
    text-align: right;
    font-size: 28px;
    font-weight: 700;
    line-height: 1.05;
    color: var(--ink);
  }
  .divider {
    position: absolute;
    left: 34px;
    right: 34px;
    top: 196px;
    height: 1px;
    background: var(--rule);
  }
  .contact {
    position: absolute;
    right: 34px;
    top: 128px;
    list-style: none;
    text-align: right;
    font-size: 13px;
    line-height: 20px;
    color: var(--ink);
  }
  .contact li { display: flex; justify-content: flex-end; align-items: center; gap: 5px; }
  .contact svg { width: 11px; height: 11px; fill: var(--ink); }
  .person { position: absolute; left: 34px; top: 206px; }
  .person__name { font-size: 20px; font-weight: 700; letter-spacing: 0.5px; }
  .person__role { font-size: 17px; font-weight: 400; color: var(--ink-soft); }
</style>
</head>
<body>
  <section class="card card--back">
    <p class="tagline">Inspiration to<br>Dream More<br>Do More, Become More</p>
    <p class="back-url">www.brookvaneconsulting.com</p>
  </section>

  <section class="card card--front">
    <div class="brand">Brookvane<br>Consulting</div>
    <ul class="contact">
      <li>404 555 0172
        <svg viewBox="0 0 12 12" aria-hidden="true"><path d="M1 4c0-2 2-3 5-3s5 1 5 3l-2 1-1-1.5H4L3 5zM3 6h6l1 5H2z"/></svg></li>
      <li>hello@brookvanemail.com
        <svg viewBox="0 0 12 12" aria-hidden="true"><path d="M0 2h12v8H0zM1 3l5 4 5-4z" fill-rule="evenodd"/></svg></li>
      <li>www.brookvaneconsulting.com
        <svg viewBox="0 0 12 12" aria-hidden="true"><circle cx="6" cy="6" r="5.5"/></svg></li>
    </ul>
    <div class="divider"></div>
    <div class="person">
      <p class="person__name">MARCUS ELLERY</p>
      <p class="person__role">Managing Director</p>
    </div>
  </section>
</body>
</html>
```